BLS Business Card 2018

Larkmere Chiropractic. We have two locations that we want to advertise on the same card. Brightvale OrthoCore campus address: 3815 Pellham Dr., Suite 240, Flowood, MS 39417. Madison address: 246 Willowmere Dr., Building D., Madison, MS 39284. website: www.drlarkmere-example.com. o:(601)555-0147 f:(601)555-0183

Target Market(s)

Health care decision makers: primary care doctors and mothers

Contact Information for Business Card

I have no idea; up for any suggestions and I'd do much better picking from examples versus describing what I'm looking for. We are in a very high end location and would like the cards to look really sharp.

Requirements
Must have
• My name, Martin R Belvane, D.C.

```html
<!DOCTYPE html>
<html lang="en">
<head>
<meta charset="utf-8">
<title>Larkmere Chiropractic Business Card</title>
<link href="https://fonts.googleapis.com/css2?family=Lora:wght@400;600&display=swap" rel="stylesheet">
<style>
  :root{
    --bg:#5a5a5c;
    --card:#29292b;
    --card-edge:#343437;
    --blue:#0c5d84;
    --blue-bright:#1877c5;
    --teal:#3fb3c9;
    --line-grey:#3c4a50;
    --emboss:#3a3a3d;
    --emboss-light:#4a4a4e;
    --white:#f4f6f8;
    --muted:#5d6166;
  }
  *{box-sizing:border-box;margin:0;padding:0}
  html,body{width:799px;height:1200px;overflow:hidden}
  body{background:var(--bg);font-family:"Lora",Georgia,serif;color:var(--white);position:relative}
  .card{position:absolute;left:50px;width:700px;height:400px;background:var(--card);border-radius:26px;overflow:hidden;box-shadow:0 12px 30px rgba(0,0,0,.35)}
  .card--back{top:90px}
  .card--front{top:690px}

  /* back */
  .emboss-name{position:absolute;right:48px;top:52px;text-align:right;font-weight:600;color:var(--emboss);text-transform:uppercase;line-height:.95;letter-spacing:1px}
  .emboss-name .l1{font-size:56px;display:block}
  .emboss-name .l2{font-size:40px;display:block}
  .band{position:absolute;left:0;right:0;top:200px;height:110px;background:var(--blue)}
  .campus-pill{position:absolute;left:50%;top:180px;transform:translateX(-50%);background:var(--card);border:2px solid var(--white);border-radius:22px;padding:8px 30px;font-weight:600;font-size:17px;white-space:nowrap}
  .address{position:absolute;top:238px;font-size:17px;line-height:1.35;display:flex;gap:10px}
  .address--left{left:40px}
  .address--right{right:30px}
  .address svg{flex:none;margin-top:3px}
  .band-divider{position:absolute;left:355px;top:232px;width:1px;height:56px;background:rgba(255,255,255,.45)}
  .web-row{position:absolute;left:0;right:0;top:336px;display:flex;justify-content:center;align-items:center;gap:24px;font-size:18px}
  .dash{width:60px;height:3px;background:linear-gradient(90deg,transparent,var(--white))}
  .dash--r{background:linear-gradient(90deg,var(--white),transparent)}

  /* front */
  .brand{position:absolute;left:120px;top:58px;display:flex;align-items:center;gap:16px}
  .brand-dot{width:20px;height:20px;border-radius:50%;background:var(--blue-bright)}
  .brand-name{font-weight:600;text-transform:uppercase;color:var(--blue-bright);line-height:.95;letter-spacing:1px}
  .brand-name .l1{display:block;font-size:52px}
  .brand-name .l2{display:block;font-size:40px}
  .person{position:absolute;left:40px;top:178px}
  .person-name{color:var(--blue-bright);font-size:25px;font-weight:600}
  .person-role{color:var(--muted);font-size:13px;margin-top:2px}
  .front-waves{position:absolute;left:0;top:0}
  .contacts{position:absolute;right:28px;top:290px;list-style:none;font-size:17px;line-height:1.35}
  .contacts li{display:flex;justify-content:flex-end;align-items:center;gap:12px}
  .contacts svg{flex:none}
</style>
</head>
<body>

<section class="card card--back" aria-label="Card back with locations">
  <div class="emboss-name"><span class="l1">Larkmere</span><span class="l2">Chiropractic</span></div>
  <div class="band"></div>
  <div class="campus-pill">OrthoCore Campus</div>
  <div class="address address--left">
    <svg width="12" height="16" viewBox="0 0 12 16"><path d="M6 0a6 6 0 0 1 6 6c0 4-6 10-6 10S0 10 0 6a6 6 0 0 1 6-6z" fill="#fff"/><circle cx="6" cy="6" r="2.3" fill="#0c5d84"/></svg>
    <p>3815 Pellham Dr., Suite 240,<br>Flowood, MS 39417</p>
  </div>
  <div class="band-divider"></div>
  <div class="address address--right">
    <svg width="12" height="16" viewBox="0 0 12 16"><path d="M6 0a6 6 0 0 1 6 6c0 4-6 10-6 10S0 10 0 6a6 6 0 0 1 6-6z" fill="#fff"/><circle cx="6" cy="6" r="2.3" fill="#0c5d84"/></svg>
    <p>246 Willowmere Dr., Building D.,<br>Madison, MS 39284</p>
  </div>
  <div class="web-row"><span class="dash"></span><span>www.drlarkmere-example.com</span><span class="dash dash--r"></span></div>
</section>

<section class="card card--front" aria-label="Card front with contact details">
  <svg class="front-waves" width="700" height="400" viewBox="0 0 700 400">
    <path d="M0 215 C90 330 300 330 440 300 C560 275 640 265 700 300 L700 400 L0 400Z" fill="var(--blue)"/>
    <path d="M0 215 C60 290 200 315 330 316 C220 305 80 275 20 222Z" fill="var(--teal)"/>
    <path d="M40 250 C160 320 330 310 450 285 C560 262 640 255 700 280 L700 295 C640 268 560 275 450 300 C330 326 170 325 40 250Z" fill="var(--card)"/>
    <path d="M300 300 C430 270 560 250 700 268" stroke="var(--line-grey)" stroke-width="7" fill="none"/>
  </svg>
  <div class="brand">
    <span class="brand-dot"></span>
    <div class="brand-name"><span class="l1">Larkmere</span><span class="l2">Chiropractic</span></div>
  </div>
  <div class="person">
    <p class="person-name">Martin R Belvane, D.C.</p>
    <p class="person-role">Managing Director</p>
  </div>
  <ul class="contacts">
    <li>(601)555-0147
      <svg width="16" height="14" viewBox="0 0 16 14"><path d="M1 4c0-3 14-3 14 0v1h-4V3H5v2H1z M3 7h10l1 6H2z" fill="#fff"/></svg></li>
    <li>(601)555-0183
      <svg width="16" height="14" viewBox="0 0 16 14"><rect x="4" y="0" width="8" height="4" fill="#fff"/><rect x="1" y="5" width="14" height="6" rx="1" fill="#fff"/><rect x="4" y="9" width="8" height="5" fill="#fff" stroke="#0c5d84"/></svg></li>
    <li>m.r.belvane@drlarkmere-example.com
      <svg width="16" height="12" viewBox="0 0 16 12"><rect width="16" height="12" fill="#fff"/><path d="M0 0l8 7 8-7" stroke="#0c5d84" stroke-width="1.5" fill="none"/></svg></li>
    <li>www.drlarkmere-example.com
      <svg width="15" height="15" viewBox="0 0 16 16"><circle cx="8" cy="8" r="7" fill="#fff"/><path d="M1 8h14M8 1v14M3 4h10M3 12h10" stroke="#0c5d84" stroke-width="1"/><ellipse cx="8" cy="8" rx="3" ry="7" stroke="#0c5d84" fill="none"/></svg></li>
  </ul>
</section>

</body>
</html>
```